Flag Order

We were just looking to order some branding flags to put on our rental equipment for our business. We would like different examples of the colors, shapes, sizes, backgrounds etc. Was thinking of just doing the plains icon instead of the whole logo on there. but open to ideas. preferably not a white background as they could get dirty,

```html
<!DOCTYPE html>
<html lang="en">
<head>
<meta charset="utf-8">
<title>Ridgeway Rentals – Branding Flag</title>
<link rel="stylesheet" href="https://fonts.googleapis.com/css2?family=Lexend:wght@500;600&display=swap">
<style>
  :root {
    --backdrop: #4e4e4e;
    --flag-blue: #0097e6;
    --flag-text: #ffffff;
  }
  html, body {
    margin: 0;
    padding: 0;
    width: 1200px;
    height: 1200px;
    overflow: hidden;
    background: var(--backdrop);
  }
  .canvas {
    position: relative;
    width: 1200px;
    height: 1200px;
  }
  .flag {
    position: absolute;
    left: 420px;
    top: 100px;
    width: 360px;
    height: 1000px;
    background: var(--flag-blue);
    font-family: "Lexend", sans-serif;
    color: var(--flag-text);
  }
  .flag__brand {
    position: absolute;
    left: 56px;
    top: 82px;
    display: flex;
    align-items: center;
    gap: 12px;
    font-weight: 600;
    font-size: 34px;
    letter-spacing: 0.02em;
    line-height: 1;
  }
  .flag__brand-mark {
    width: 26px;
    height: 26px;
    border-radius: 50%;
    background: var(--flag-text);
  }
  .flag__headline {
    position: absolute;
    left: 56px;
    top: 390px;
    margin: 0;
    font-weight: 500;
    font-size: 58px;
    line-height: 1.15;
  }
</style>
</head>
<body>
  <main class="canvas">
    <section class="flag" aria-label="Ridgeway Rentals branding flag">
      <div class="flag__brand">
        <span class="flag__brand-mark" aria-hidden="true"></span>
        <span class="flag__brand-name">Ridgeway Rentals</span>
      </div>
      <h1 class="flag__headline">Pushing<br>You<br>Futher</h1>
    </section>
  </main>
</body>
</html>
```